Law Offices business card

Hi there, I'll need business card for the Law Offices of Colin Matheny. The information must convey his strategic approach and quick resolution to complex business litigation needs. Please emphasize Civil Litigation, Corporate Law, Business Governance and Real Estate Law. Colin has over 25 years of experience in these fields.The card should be modern and edgy and the message should be clear. Please consult his current website for ideas.

```html
<!DOCTYPE html>
<html lang="en">
<head>
<meta charset="utf-8">
<title>Law Offices of Colin Matheny – Business Card</title>
<link href="https://fonts.googleapis.com/css2?family=Libre+Baskerville&family=Open+Sans:wght@400;700&display=swap" rel="stylesheet">
<style>
  :root {
    --stage: #3a3a3c;
    --card: #242424;
    --ink: #bdbacd;
    --ink-soft: #a9a7b8;
    --accent: #e2312b;
  }
  * { margin: 0; padding: 0; box-sizing: border-box; }
  html, body { width: 1200px; height: 900px; overflow: hidden; }
  body {
    background: var(--stage);
    font-family: "Open Sans", Arial, sans-serif;
    color: var(--ink);
    position: relative;
  }
  .card {
    position: absolute;
    left: 250px;
    width: 700px;
    height: 400px;
    background: var(--card);
    box-shadow: 0 10px 30px rgba(0,0,0,.45);
  }
  .card--front { top: 30px; }
  .card--back { top: 470px; }

  .wordmark {
    position: absolute;
    display: flex;
    align-items: flex-start;
    gap: 14px;
    font-family: "Libre Baskerville", Georgia, serif;
    font-weight: 400;
    color: var(--ink);
  }
  .wordmark__square {
    width: 18px; height: 18px;
    background: var(--accent);
    margin-top: 10px;
    flex: none;
  }
  .wordmark__text { line-height: 1.05; }
  .wordmark__pre { display: block; text-transform: uppercase; letter-spacing: 2px; }
  .wordmark__name { display: block; }

  .card--front .wordmark { left: 150px; top: 120px; }
  .card--front .wordmark__pre { font-size: 17px; }
  .card--front .wordmark__name { font-size: 44px; }

  .practice {
    position: absolute;
    left: 300px; top: 232px;
    list-style: none;
    font-size: 14px;
    text-transform: uppercase;
    line-height: 1.45;
    color: var(--ink-soft);
  }
  .practice__item--accent { color: var(--accent); padding-left: 40px; }

  .card--back .wordmark { left: 40px; top: 55px; }
  .card--back .wordmark__pre { font-size: 15px; }
  .card--back .wordmark__name { font-size: 38px; }

  .person {
    position: absolute;
    right: 40px; top: 180px;
    text-align: right;
  }
  .person__name { font-size: 21px; font-weight: 700; letter-spacing: .5px; text-transform: uppercase; }
  .person__role { font-size: 11px; color: var(--accent); text-transform: uppercase; letter-spacing: 1px; }

  .divider {
    position: absolute;
    left: 30px; top: 238px;
    width: 600px; height: 1px;
    background: var(--ink-soft);
  }

  .contacts {
    position: absolute;
    right: 40px; top: 250px;
    list-style: none;
    font-size: 14px;
    line-height: 19px;
    text-align: right;
    color: var(--ink);
  }
  .contacts li { display: flex; justify-content: flex-end; align-items: center; gap: 10px; }
  .contacts svg { width: 12px; height: 12px; fill: none; stroke: var(--accent); stroke-width: 2; }

  .address {
    position: absolute;
    left: 40px; top: 330px;
    font-size: 15px;
    line-height: 20px;
    font-style: normal;
    color: var(--ink-soft);
  }
</style>
</head>
<body>
  <section class="card card--front">
    <div class="wordmark">
      <span class="wordmark__square"></span>
      <span class="wordmark__text">
        <span class="wordmark__pre">Law Offices of</span>
        <span class="wordmark__name">Colin Matheny, PA</span>
      </span>
    </div>
    <ul class="practice">
      <li class="practice__item">Civil Litigation · Corporate Law</li>
      <li class="practice__item practice__item--accent">Real Estate Law</li>
      <li class="practice__item">Business Governance · 25+ Years</li>
    </ul>
  </section>

  <section class="card card--back">
    <div class="wordmark">
      <span class="wordmark__square"></span>
      <span class="wordmark__text">
        <span class="wordmark__pre">Law Offices of</span>
        <span class="wordmark__name">Colin Matheny, PA</span>
      </span>
    </div>

    <div class="person">
      <div class="person__name">Colin Matheny</div>
      <div class="person__role">Attorney</div>
    </div>

    <div class="divider"></div>

    <ul class="contacts">
      <li>561-555-0142
        <svg viewBox="0 0 12 12"><path d="M2 1.5l2 0 1 2.5-1.2 1a6 6 0 0 0 3.2 3.2l1-1.2 2.5 1v2a1 1 0 0 1-1 1A9 9 0 0 1 1 2.5a1 1 0 0 1 1-1z"/></svg>
      </li>
      <li>561-555-0187
        <svg viewBox="0 0 12 12"><rect x="3" y="1" width="6" height="3"/><rect x="1" y="4" width="10" height="5"/><rect x="3" y="7" width="6" height="4"/></svg>
      </li>
      <li>colin@mathenylaw.com
        <svg viewBox="0 0 12 12"><rect x="1" y="2.5" width="10" height="7"/><path d="M1 2.5l5 4 5-4"/></svg>
      </li>
      <li>www.mathenylaw.com
        <svg viewBox="0 0 12 12"><circle cx="6" cy="6" r="5"/><path d="M1 6h10M6 1c-2.5 3-2.5 7 0 10M6 1c2.5 3 2.5 7 0 10"/></svg>
      </li>
    </ul>

    <address class="address">118B Harbor Lane<br>Lakeview, FL 33401</address>
  </section>
</body>
</html>
```